VENTURE CAPITAL GROUP BUSINESS CARD DESIGN

Venture Capital Group based in SF looking for a bold business card design. No trendy colour explosion, 3D effects etc. Just "simple" optical effects. Works on your brain, keeps your eye focused and sticks to your mind.
Target Market(s)
Technology startups
Industry/Entity Type
Venture Capital
Contact Information for Business Card
DESMOND WHITLAKE
MANAGING PARTNER
187 FENWORTH ST SAN FRANCISCO, CA 94187
415.555.0142 O
415.555.0147 F
415.555.0193 C
desmond@veldtmoorcapital.ventures

```html
<!DOCTYPE html>
<html lang="en">
<head>
<meta charset="utf-8">
<title>Veldtmoor Capital Group — Business Card</title>
<link href="https://fonts.googleapis.com/css2?family=EB+Garamond:wght@400;600;700&display=swap" rel="stylesheet">
<style>
  :root {
    --stage: #2b2b2b;
    --green-deep: #0f6a24;
    --green-mid: #2a9a3c;
    --green-light: #4fbf4a;
    --ink: #1c1c1c;
    --paper: #f4f4f4;
    --paper-shade: #d9d9d9;
    --white: #ffffff;
  }
  * { margin: 0; padding: 0; box-sizing: border-box; }
  html, body { width: 1200px; height: 873px; overflow: hidden; }
  body {
    background: var(--stage);
    font-family: "EB Garamond", Georgia, serif;
    position: relative;
  }
  .card {
    position: absolute;
    top: 286px;
    width: 525px;
    height: 300px;
    box-shadow: 0 14px 30px rgba(0,0,0,.5);
    overflow: hidden;
  }
  .card-front {
    left: 50px;
    background: radial-gradient(ellipse at 70% 20%, var(--green-light) 0%, var(--green-mid) 40%, var(--green-deep) 100%);
    display: flex;
    align-items: center;
    justify-content: center;
  }
  .front-wordmark {
    color: var(--white);
    font-weight: 400;
    font-size: 34px;
    letter-spacing: 1px;
    display: flex;
    align-items: center;
    gap: 14px;
  }
  .wordmark-dot {
    width: 16px; height: 16px;
    border-radius: 50%;
    background: currentColor;
  }
  .card-back {
    left: 625px;
    background: var(--paper);
  }
  .back-texture {
    position: absolute; inset: 0;
    background: linear-gradient(135deg, var(--white) 0%, var(--paper) 45%, var(--paper-shade) 100%);
  }
  .holder {
    position: absolute;
    top: 30px; left: 0; right: 0;
    text-align: center;
  }
  .holder-name {
    color: var(--green-deep);
    font-weight: 700;
    font-size: 24px;
    line-height: 1;
  }
  .holder-role {
    color: var(--ink);
    font-size: 12px;
    margin-top: 4px;
  }
  .back-wordmark {
    position: absolute;
    left: 30px; top: 150px;
    width: 210px;
    color: var(--green-deep);
    font-size: 26px;
    line-height: 1.1;
    text-align: center;
  }
  .divider {
    position: absolute;
    left: 258px; top: 110px;
    width: 1px; height: 110px;
    background: linear-gradient(var(--paper), #8a8a8a, var(--paper));
  }
  .contact-list {
    position: absolute;
    left: 276px; top: 104px;
    list-style: none;
  }
  .contact-list li {
    display: flex;
    align-items: center;
    gap: 8px;
    font-size: 13.5px;
    color: var(--ink);
    height: 24px;
  }
  .contact-icon {
    width: 17px; height: 17px;
    flex: none;
  }
  .site-url {
    position: absolute;
    left: 0; right: 0; bottom: 26px;
    text-align: center;
    font-weight: 700;
    font-size: 15px;
    letter-spacing: .5px;
    color: var(--ink);
  }
</style>
</head>
<body>

<section class="card card-front">
  <div class="front-wordmark"><span class="wordmark-dot"></span>Veldtmoor Capital Group</div>
</section>

<section class="card card-back">
  <div class="back-texture" role="img" aria-label="Faint light grey faceted polygon background texture"></div>

  <div class="holder">
    <p class="holder-name">Desmond Whitlake</p>
    <p class="holder-role">Managing Partner</p>
  </div>

  <div class="back-wordmark">Veldtmoor Capital Group</div>

  <div class="divider"></div>

  <ul class="contact-list">
    <li>
      <svg class="contact-icon" viewBox="0 0 20 20"><circle cx="10" cy="10" r="10" fill="var(--green-mid)"/><rect x="5" y="8" width="10" height="6" rx="1" fill="#fff"/><path d="M5 8 Q10 3 15 8" stroke="#fff" stroke-width="1.6" fill="none"/></svg>
      415.555.0142
    </li>
    <li>
      <svg class="contact-icon" viewBox="0 0 20 20"><circle cx="10" cy="10" r="10" fill="var(--green-mid)"/><rect x="5" y="9" width="10" height="5" rx="1" fill="#fff"/><rect x="7" y="5" width="6" height="4" fill="#fff"/></svg>
      415.555.0147
    </li>
    <li>
      <svg class="contact-icon" viewBox="0 0 20 20"><circle cx="10" cy="10" r="10" fill="var(--green-mid)"/><path d="M6.5 5.5 L8.5 5 L9.5 8 L8.3 9 Q9.5 11.5 11 12 L12 10.8 L15 11.8 L14.5 13.8 Q9 14.5 6.5 5.5Z" fill="#fff"/></svg>
      415.555.0193
    </li>
    <li>
      <svg class="contact-icon" viewBox="0 0 20 20"><circle cx="10" cy="10" r="10" fill="var(--green-mid)"/><rect x="5" y="6.5" width="10" height="7" fill="#fff"/><path d="M5 6.5 L10 11 L15 6.5" stroke="var(--green-mid)" stroke-width="1" fill="none"/></svg>
      desmond@veldtmoorcapital.ventures
    </li>
    <li>
      <svg class="contact-icon" viewBox="0 0 20 20"><circle cx="10" cy="10" r="10" fill="var(--green-mid)"/><path d="M10 15 Q6 10.5 6 8.5 A4 4 0 0 1 14 8.5 Q14 10.5 10 15Z" fill="#fff"/><circle cx="10" cy="8.5" r="1.5" fill="var(--green-mid)"/></svg>
      187 Fenworth St San Francisco, CA 94187
    </li>
  </ul>

  <p class="site-url">www.veldtmoorcapital.ventures.com</p>
</section>

</body>
</html>
```